UX - Need some screens design for a Skill Assessment Application

I am building an app to carry out skill assessments. Depending on how the assessment is configured, it may have one or more parts
1. Question based assessment (Multiple Choice, True False, Fill in the blanks"
2. Endorsement by two colleagues - A screen that allows user to pick colleagues based on search and shows the status of pending requests
3. A written submission - a page that explains the format of the submission and a file upload
As each assessment can be configured with or without any of the steps, the assessment UI must be such that these areas get hidden/displayed based on configuration.
Colour codes to be used can be #0e78bb and #ffffff
There will also be a start screen (instructions) and an end screen (results)
Target Market(s)
Enterprise software
Number of Pages Required
4 page

```html
<!DOCTYPE html>
<html lang="en">
<head>
<meta charset="utf-8">
<title>New Endorsement Request</title>
<link href="https://fonts.googleapis.com/css2?family=Inter:wght@400;500;600;700&display=swap" rel="stylesheet">
<style>
  :root {
    --brand: #0052a8;
    --accent: #0e78bb;
    --link: #1a8bd1;
    --white: #ffffff;
    --page: #f5f7f9;
    --ink: #222831;
    --muted: #5d636b;
    --line: #dfe3e8;
    --head-bg: #e9f5fc;
    --more-bg: #dddddd;
    --t1: #8a5a34; --t2: #2f2f2f; --t3: #8d8d8d; --t4: #a07a58;
    --t5: #e8b77c; --t6: #5a4636; --t7: #7d6f4e; --t8: #79b8d6;
    --t9: #3a5aa0; --t10: #c9c6c2; --t11: #8e1c1c; --t12: #d6c95a; --t13: #b2773f;
  }
  * { box-sizing: border-box; margin: 0; padding: 0; }
  html, body { width: 1200px; height: 686px; overflow: hidden; }
  body { font-family: "Inter", Arial, sans-serif; background: var(--page); color: var(--ink); }

  .topbar { height: 43px; background: var(--brand); display: flex; align-items: center; padding: 0 57px; }
  .brand { display: flex; align-items: center; gap: 10px; color: var(--white); font-size: 15px; font-weight: 600; }
  .brand-dot { width: 20px; height: 20px; border-radius: 50%; background: var(--white); }
  .main-nav { margin-left: auto; display: flex; align-items: center; gap: 21px; }
  .main-nav a { color: #d6e4f3; text-decoration: none; font-size: 12.5px; }
  .main-nav a.is-active { color: var(--white); font-weight: 700; }
  .profile { display: flex; align-items: center; gap: 4px; margin-left: 4px; }
  .profile .avatar { width: 27px; height: 27px; border: 1.5px solid var(--white); }

  .page-head { background: var(--white); height: 97px; border-bottom: 1px solid var(--line); padding: 0 57px; position: relative; }
  .crumbs { position: absolute; top: 22px; left: 57px; display: flex; align-items: center; gap: 7px; font-size: 11.5px; color: var(--muted); }
  .crumbs a { color: var(--link); text-decoration: none; margin-left: 6px; }
  .title { position: absolute; top: 56px; left: 88px; display: flex; align-items: center; gap: 12px; font-size: 21px; font-weight: 600; }

  .endorse-table { position: absolute; top: 161px; left: 88px; width: 1024px; background: var(--white); border: 1px solid var(--line); border-radius: 4px; overflow: hidden; }
  .row { display: flex; align-items: center; height: 61px; padding: 0 17px; border-top: 1px solid var(--line); font-size: 12.5px; }
  .row.head { height: 42px; border-top: 0; background: var(--head-bg); color: var(--muted); font-weight: 500; }
  .col-user { width: 55px; color: var(--muted); }
  .head .col-user { color: var(--muted); }
  .col-cat { flex: 1; font-weight: 500; }
  .head .col-cat { font-weight: 500; }
  .col-endorse { display: flex; align-items: center; gap: 4px; }
  .open-btn { width: 28px; height: 28px; border-radius: 50%; background: var(--accent); display: flex; align-items: center; justify-content: center; margin-left: 13px; }
  .avatar { width: 27px; height: 27px; border-radius: 50%; display: inline-block; flex: none; }
  .more { background: var(--more-bg); font-size: 10.5px; font-weight: 700; display: inline-flex; align-items: center; justify-content: center; color: var(--ink); }
  .a1{background:var(--t1)}.a2{background:var(--t2)}.a3{background:var(--t3)}.a4{background:var(--t4)}
  .a5{background:var(--t5)}.a6{background:var(--t6)}.a7{background:var(--t7)}.a8{background:var(--t8)}
  .a9{background:var(--t9)}.a10{background:var(--t10)}.a11{background:var(--t11)}.a12{background:var(--t12)}.a13{background:var(--t13)}
</style>
</head>
<body>
<header class="topbar">
  <div class="brand"><span class="brand-dot"></span>LogoPlaceholder</div>
  <nav class="main-nav">
    <a href="#">Assessments</a>
    <a href="#" class="is-active">Endorsement</a>
    <a href="#">Submissions</a>
    <a href="#">Results</a>
    <span class="profile">
      <span class="avatar a9" role="img" aria-label="Profile photo of signed-in user"></span>
      <svg width="10" height="10" viewBox="0 0 10 10"><path d="M2 3.5l3 3 3-3" fill="none" stroke="#fff" stroke-width="1.5"/></svg>
    </span>
  </nav>
</header>

<section class="page-head">
  <div class="crumbs">
    <svg width="20" height="20" viewBox="0 0 20 20"><circle cx="10" cy="10" r="8.8" fill="none" stroke="#0e78bb" stroke-width="1.6"/><path d="M14 10H6.5M9.5 6.8L6.3 10l3.2 3.2" fill="none" stroke="#0e78bb" stroke-width="1.6" stroke-linecap="round" stroke-linejoin="round"/></svg>
    <a href="#">Endorsement</a><span>/</span><span>New Endorsement Request</span>
  </div>
  <h1 class="title">
    <svg width="22" height="22" viewBox="0 0 22 22" fill="none" stroke="#444" stroke-width="1.3" stroke-linejoin="round"><path d="M11 2l1.3 2.7 3 .4-2.2 2 .6 3-2.7-1.5-2.7 1.5.6-3-2.2-2 3-.4z"/><path d="M2 13h3v7H2zM5 14h4l3 1.5h3a1.2 1.2 0 010 2.4H11M5 19h9l5-3a1.3 1.3 0 00-1.4-2.2L15 15"/></svg>
    New Endorsement Request
  </h1>
</section>

<section class="endorse-table">
  <div class="row head"><span class="col-user">User</span><span class="col-cat">Endorsements Category</span><span>Endorsements</span></div>

  <div class="row"><span class="col-user">24</span><span class="col-cat">Application Design Capabilities</span>
    <span class="col-endorse" role="img" aria-label="Photos of endorsing colleagues">
      <span class="avatar a13"></span><span class="avatar a2"></span><span class="avatar a3"></span><span class="avatar a4"></span><span class="avatar a5"></span><span class="avatar a6"></span><span class="avatar a7"></span><span class="avatar a8"></span><span class="avatar a9"></span><span class="avatar a10"></span><span class="avatar a11"></span><span class="avatar a12"></span><span class="avatar a1"></span><span class="avatar more">11+</span>
    </span>
    <span class="open-btn"><svg width="10" height="10" viewBox="0 0 10 10"><path d="M4 2.5L6.5 5 4 7.5" fill="none" stroke="#fff" stroke-width="1.5" stroke-linecap="round"/></svg></span>
  </div>

  <div class="row"><span class="col-user">8</span><span class="col-cat">UI/UX Designer</span>
    <span class="col-endorse" role="img" aria-label="Photos of endorsing colleagues">
      <span class="avatar a2"></span><span class="avatar a9"></span><span class="avatar a4"></span><span class="avatar a7"></span><span class="avatar a5"></span><span class="avatar a13"></span><span class="avatar a6"></span><span class="avatar a8"></span>
    </span>
    <span class="open-btn"><svg width="10" height="10" viewBox="0 0 10 10"><path d="M4 2.5L6.5 5 4 7.5" fill="none" stroke="#fff" stroke-width="1.5" stroke-linecap="round"/></svg></span>
  </div>

  <div class="row"><span class="col-user">6</span><span class="col-cat">Front-end Developer</span>
    <span class="col-endorse" role="img" aria-label="Photos of endorsing colleagues">
      <span class="avatar a2"></span><span class="avatar a3"></span><span class="avatar a5"></span><span class="avatar a6"></span><span class="avatar a7"></span><span class="avatar a8"></span>
    </span>
    <span class="open-btn"><svg width="10" height="10" viewBox="0 0 10 10"><path d="M4 2.5L6.5 5 4 7.5" fill="none" stroke="#fff" stroke-width="1.5" stroke-linecap="round"/></svg></span>
  </div>

  <div class="row"><span class="col-user">11</span><span class="col-cat">Cybersecurity Analyst</span>
    <span class="col-endorse" role="img" aria-label="Photos of endorsing colleagues">
      <span class="avatar a4"></span><span class="avatar a9"></span><span class="avatar a5"></span><span class="avatar a3"></span><span class="avatar a6"></span><span class="avatar a2"></span><span class="avatar a7"></span><span class="avatar a11"></span><span class="avatar a8"></span><span class="avatar a10"></span><span class="avatar a12"></span>
    </span>
    <span class="open-btn"><svg width="10" height="10" viewBox="0 0 10 10"><path d="M4 2.5L6.5 5 4 7.5" fill="none" stroke="#fff" stroke-width="1.5" stroke-linecap="round"/></svg></span>
  </div>

  <div class="row"><span class="col-user">8</span><span class="col-cat">DevOps Engineer</span>
    <span class="col-endorse" role="img" aria-label="Photos of endorsing colleagues">
      <span class="avatar a5"></span><span class="avatar a6"></span><span class="avatar a7"></span><span class="avatar a10"></span><span class="avatar a13"></span><span class="avatar a11"></span><span class="avatar a12"></span><span class="avatar a9"></span>
    </span>
    <span class="open-btn"><svg width="10" height="10" viewBox="0 0 10 10"><path d="M4 2.5L6.5 5 4 7.5" fill="none" stroke="#fff" stroke-width="1.5" stroke-linecap="round"/></svg></span>
  </div>

  <div class="row"><span class="col-user">4</span><span class="col-cat">Sales Representative</span>
    <span class="col-endorse" role="img" aria-label="Photos of endorsing colleagues">
      <span class="avatar a7"></span><span class="avatar a8"></span><span class="avatar a6"></span><span class="avatar a12"></span>
    </span>
    <span class="open-btn"><svg width="10" height="10" viewBox="0 0 10 10"><path d="M4 2.5L6.5 5 4 7.5" fill="none" stroke="#fff" stroke-width="1.5" stroke-linecap="round"/></svg></span>
  </div>
</section>
</body>
</html>
```